Web Design for Independent Pet Supply shop.

Larch Critter Depot is a locally owned and operated premium natural pet food store and supply company with 2 thriving retail stores in Bend, Oregon, and a home delivery service. The pet food offered is the best on the market and may be described as “holistic”. Also on offer is a vast selection of toys, training tools, treats, and other supplies, as well as dog washing services that range from "do-it yourself" to "spa." Current site: LarchCritterDepot.com. They need a new, updated and responsive site.
Likes:
Tovanels.com: Natural colors, not loud, pages in motion, simple & clean but very informative.
Dorvikmerin.com: Everything in simple big colorful blocks. The specials run across the top and in motion. This site looks very professional but simple. The information is available several different places.
Plenharvest.com: Again big blocks through out. Very Fun and inviting. Tons of information with videos and recipes and testimonials. Pleasant feel and colors as well.
Dislikes:
Furlix.com: Looks cheap, hate the colors, very busy and over whelming. Hate the old style header bar going across with options. Too many printed words instead of fun images.
Colors should be "natural" tones, warm and soothing. Deep dark blue and greys with earthy wood color.
Do Not Use: Blue violet, violet, red violet

```html
<!DOCTYPE html>
<html lang="en">
<head>
<meta charset="utf-8">
<title>Larch Critter Depot</title>
<link rel="stylesheet" href="https://fonts.googleapis.com/css2?family=Ubuntu:wght@400;500;700&family=Open+Sans:wght@400;600;700&family=Signika:wght@400;600&display=swap">
<style>
:root{
  --navy:#0f1a2e;
  --navy-deep:#0b1426;
  --tan:#b39a5f;
  --tan-dark:#a38a52;
  --gold:#c9a65c;
  --orange:#c8955a;
  --grey-bar:#c6c6c6;
  --ink:#1b1b1b;
  --body:#555;
  --white:#fff;
  --muted:#b8bccb;
}
*{margin:0;padding:0;box-sizing:border-box}
html,body{width:670px;height:1200px;overflow:hidden;background:var(--white)}
body{position:relative;font-family:"Open Sans",Arial,sans-serif;color:var(--body)}
.section{position:absolute;left:0;width:670px}
.social-dots{display:inline-flex;gap:5px;vertical-align:middle}
.social-dots i{display:block;width:6px;height:6px;border-radius:50%;background:var(--orange)}

/* top bar */
.top-bar{top:0;height:22px;background:var(--grey-bar);font-size:5px;font-weight:600;color:#333;letter-spacing:.2px}
.top-bar .connect{position:absolute;left:80px;top:8px}
.top-bar .account{position:absolute;right:80px;top:8px}

/* nav */
.main-nav{top:22px;height:44px;background:var(--navy)}
.main-nav a{position:absolute;top:18px;color:var(--white);font-family:"Ubuntu",sans-serif;font-size:6.5px;font-weight:500;text-decoration:none;letter-spacing:.3px}
.main-nav .home-dot{position:absolute;left:112px;top:9px;width:6px;height:6px;border-radius:50%;background:var(--orange)}
.brand{position:absolute;left:280px;top:16px;display:flex;align-items:center;gap:4px;white-space:nowrap}
.brand .mark{width:9px;height:9px;border-radius:50%;background:var(--gold)}
.brand span{font-family:"Ubuntu",sans-serif;font-weight:700;font-size:9px;color:var(--gold)}

/* hero */
.hero{top:66px;height:276px;background:linear-gradient(90deg,#8a7a3c 0%,#b58a4c 25%,#7d8a3a 55%,#7b8f3d 80%,#6a7f35 100%)}
.hero-photo{position:absolute;inset:0}
.slider-tab{position:absolute;top:96px;width:44px;height:42px;background:linear-gradient(#d9c08a,#b39158);border-radius:50%}
.slider-tab.prev{left:-22px}
.slider-tab.next{right:-22px}
.hero-card{position:absolute;left:434px;top:90px;width:153px;height:132px;background:var(--navy);border:1px solid #2c3548;padding:20px 0 0 13px;overflow:hidden}
.hero-card p{font-family:"Signika",sans-serif;font-size:18px;line-height:23px;color:var(--white);text-transform:uppercase;white-space:nowrap}
.hero-card .gold{color:var(--gold);font-weight:600}

/* news */
.news{top:342px;height:252px;background:var(--tan)}
.section-title{position:absolute;left:0;width:670px;text-align:center;font-family:"Ubuntu",sans-serif;font-weight:500;font-size:14px;letter-spacing:.3px}
.news .section-title{top:24px;color:var(--white)}
.news-item{position:absolute;top:70px;width:150px;text-align:center}
.news-icon{margin:0 auto;width:48px;height:48px;border-radius:50%;border:3px solid var(--white);background:var(--gold);display:flex;align-items:center;justify-content:center}
.news-icon i{display:block;width:24px;height:24px;border-radius:50%;background:var(--navy)}
.news-item h3{margin-top:9px;font-family:"Ubuntu",sans-serif;font-weight:500;font-size:7.5px;color:var(--navy);letter-spacing:.2px;white-space:nowrap}
.news-item p{margin-top:16px;font-size:4.7px;line-height:10.7px;color:var(--white)}
.news-item p strong{font-weight:700}
.news-item p.lead{font-size:8px;line-height:10px;font-weight:600}
.btn-more{position:absolute;top:212px;width:44px;height:15px;background:var(--navy);color:var(--white);font-size:5.5px;font-weight:600;line-height:15px;text-align:center;border-radius:2px}

/* blog */
.blog{top:594px;height:318px;background:var(--white)}
.blog .section-title{top:28px;color:var(--ink)}
.post{position:absolute;top:61px;width:161px}
.post-image{width:161px;height:99px}
.post h3{margin-top:6px;font-family:"Ubuntu",sans-serif;font-weight:500;font-size:10.5px;line-height:16px;color:var(--ink)}
.post p{margin-top:8px;font-size:4.8px;line-height:10.7px;color:var(--body)}
.post .read-more{display:block;margin-top:1px;font-size:4.5px;font-weight:700;color:var(--ink)}
.post-meta{position:absolute;top:209px;left:0;width:161px;height:19px;background:#f0f0f0;border:1px solid #ddd;font-size:4.5px;color:#333;display:flex;align-items:center;justify-content:space-between;padding:0 7px}
.post-meta .share{display:flex;align-items:center;gap:4px}
.post-meta .social-dots{gap:4px}
.post-meta .social-dots i{width:5px;height:5px}

/* newsletter */
.newsletter{top:912px;height:64px;background:var(--tan)}
.newsletter h4{position:absolute;left:107px;top:25px;font-family:"Ubuntu",sans-serif;font-weight:500;font-size:9.8px;color:var(--navy);display:flex;align-items:center;gap:6px;white-space:nowrap}
.newsletter h4 svg{display:block}
.newsletter .email{position:absolute;left:258px;top:24px;width:245px;height:22px;background:var(--white);border-radius:2px;font-size:4.8px;color:#666;padding:8px 6px}
.newsletter .subscribe{position:absolute;left:510px;top:25px;width:77px;height:20px;background:var(--orange);border-radius:2px;color:var(--white);font-family:"Ubuntu",sans-serif;font-weight:500;font-size:7.5px;line-height:20px;text-align:center}

/* footer */
.site-footer{top:976px;height:224px;background:var(--navy-deep);color:var(--white)}
.footer-col{position:absolute;top:30px}
.footer-col h5{font-family:"Ubuntu",sans-serif;font-weight:500;font-size:5.8px;letter-spacing:.2px;display:flex;align-items:center;gap:4px}
.footer-col h5 i{display:block;width:5px;height:5px;border-radius:50%;background:var(--orange)}
.footer-col ul{list-style:none;margin-top:25px}
.footer-col li{font-size:5.8px;line-height:13.4px;color:#e6e8ee}
.page-box{position:absolute;left:254px;top:61px;width:134px;height:90px;background:var(--white);border:1px solid #c9d1df;color:#333}
.page-box .head{height:12px;background:#eef1f6;border-bottom:1px solid #d5dbe6;font-size:4.8px;font-weight:700;padding:3px 4px}
.page-box .brand-row{display:flex;align-items:center;gap:6px;padding:5px 4px 0}
.page-box .brand-row b{font-family:"Ubuntu",sans-serif;font-size:6px;color:var(--gold)}
.page-box .like{font-size:4.2px;border:1px solid #ccd;padding:1px 3px;border-radius:2px;color:#333}
.page-box .count{font-size:4.2px;border:1px solid #ccd;padding:1px 3px}
.avatars{display:flex;gap:3px;padding:5px 4px 0}
.avatar{width:22px;text-align:center;font-size:3.8px;color:#555}
.avatar .pic{width:22px;height:22px;background:linear-gradient(#9a8f84,#5b5550)}
.page-box .foot{position:absolute;left:4px;bottom:3px;font-size:3.8px;color:#4b5a78;display:flex;align-items:center;gap:2px}
.page-box .foot i{display:block;width:5px;height:5px;background:#4b5a78}
.slide-arrows{position:absolute;left:574px;top:30px;font-size:8px;letter-spacing:6px}
.tweet{position:absolute;left:414px;width:180px}
.tweet .thumb{position:absolute;left:0;top:0;width:40px;height:33px}
.tweet .body{position:absolute;left:43px;top:0;width:135px}
.tweet .handle{font-size:5.3px;color:var(--gold)}
.tweet .text{margin-top:3px;font-size:4.9px;line-height:8px;color:#e6e8ee}
.tweet .actions{position:absolute;left:116px;top:52px;display:flex;gap:14px}
.tweet .actions svg{display:block}
.footer-bottom{position:absolute;top:204px;left:0;width:670px;font-size:4.6px;color:#dfe2ea}
.footer-bottom .copy{position:absolute;left:80px}
.footer-bottom .connect{position:absolute;left:478px;top:-1px}
</style>
</head>
<body>

<header class="section top-bar">
  <div class="connect">CONNECT WITH US : <span class="social-dots"><i></i><i></i><i></i><i></i><i></i><i></i></span></div>
  <div class="account">COUNTRY : US &nbsp; | &nbsp; LOGIN &nbsp; | &nbsp; SHOPPING BAG</div>
</header>

<nav class="section main-nav">
  <span class="home-dot"></span>
  <a href="#" style="left:108px">HOME</a>
  <a href="#" style="left:142px">EVENTS</a>
  <a href="#" style="left:182px">BLOG</a>
  <a href="#" style="left:215px">ABOUT</a>
  <div class="brand"><span class="mark"></span><span>LARCH CRITTER DEPOT</span></div>
  <a href="#" style="left:410px">DOG WASH</a>
  <a href="#" style="left:461px">PRODUCTS</a>
  <a href="#" style="left:512px">RESOURCES</a>
  <a href="#" style="left:564px">CONTACT</a>
</nav>

<section class="section hero">
  <div class="hero-photo" role="img" aria-label="Golden retriever smiling in a sunny green meadow"></div>
  <div class="slider-tab prev"></div>
  <div class="slider-tab next"></div>
  <div class="hero-card">
    <p><span class="gold">Dedicated</span><br>to a better<br>diet for a<br><span class="gold">healthier pet</span></p>
  </div>
</section>

<section class="section news">
  <h2 class="section-title">WHAT’S IN NEWS</h2>
  <article class="news-item" style="left:81px">
    <div class="news-icon" role="img" aria-label="Dog icon"><i></i></div>
    <h3>PUP BREW</h3>
    <p>Now you can pour some cold brew for your pup in a fun and easy way that has a delicious flavor and packed full of vegetarian K9 specific glucosamine with essential vitamins and minerals for your dogs health and well being.</p>
  </article>
  <div class="btn-more" style="left:137px">MORE</div>

  <article class="news-item" style="left:259px">
    <div class="news-icon" role="img" aria-label="Bottle icon"><i></i></div>
    <h3>NUTROVA LAWSUIT</h3>
    <p><strong>IN NEWS:</strong> Nutrova is being sued by . Daniel Merrow of Harbor Point, Oregon. He he first purchased Hearthmix food in December or January. Since, he has witnessed one of his dogs pass away and 2 of his dogs get sick. PLEASE read and watch this link for more information!</p>
  </article>
  <div class="btn-more" style="left:312px">MORE</div>

  <article class="news-item" style="left:433px">
    <div class="news-icon" role="img" aria-label="Sale shopping bag icon"><i></i></div>
    <h3>BRIGHTWELL 5/8" LEADS ON SALE</h3>
    <p>Your local Brightwell has ALL of their 5/8"</p>
    <p class="lead" style="margin-top:2px">Leads ON SALE for just $10!</p>
  </article>
  <div class="btn-more" style="left:486px">MORE</div>
</section>

<section class="section blog">
  <h2 class="section-title">BLOG POSTS</h2>

  <article class="post" style="left:80px">
    <div class="post-image" role="img" aria-label="Colorful dog wash price posters on a purple wall" style="background:linear-gradient(90deg,#5a2c3a,#6b3446 40%,#7a3a4c)"></div>
    <h3>The Larch Critter Depot Dog Wash News and Updates</h3>
    <p>The Larch Critter Depot Dog Wash attendants are always here to help wash your four-legged friends, and trim their nails...but they are also here to help educate all of us! Nail trims are such an essential routine for our pups, especially if they don’t run and walk as much as they would in the wild.</p>
    <span class="read-more">Read More&gt;&gt;</span>
    <div class="post-meta"><span>No Comments:</span><span class="share">Share : <span class="social-dots"><i></i><i></i><i></i><i></i><i></i><i></i></span></span></div>
  </article>

  <article class="post" style="left:254px">
    <div class="post-image" role="img" aria-label="20 years anniversary badge with a dog silhouette" style="background:#fff;border:1px solid #ddd;display:flex;align-items:center;justify-content:center">
      <svg width="44" height="44" viewBox="0 0 44 44" aria-hidden="true"><circle cx="22" cy="22" r="20" fill="#2b2b2b"/></svg>
    </div>
    <h3>20th Anniversary Celebration!</h3>
    <p>Come join us for our 20th Anniversary Celebration at Larch Critter Depot August 10, 2013 from 11 am to 3 pm. We are lining up lots of fun stuff for people and pets. Here is what is planned so far!</p>
    <div class="post-meta"><span>No Comments:</span><span class="share">Share : <span class="social-dots"><i></i><i></i><i></i><i></i><i></i><i></i></span></span></div>
  </article>

  <article class="post" style="left:428px">
    <div class="post-image" role="img" aria-label="Community pet food bank appeal banner" style="background:linear-gradient(#3a3a36,#222220)"></div>
    <h3>S.H.A.R.E. needs your help</h3>
    <p>Thanks to all the help and support from our community we had another successful event, this Saturday. SHARE Community Pet Food Bank registered 15 new families in addition to providing a months worth of food for 20 existing clients! This increase in need has left our shelves bare!</p>
    <div class="post-meta"><span>No Comments:</span><span class="share">Share : <span class="social-dots"><i></i><i></i><i></i><i></i><i></i><i></i></span></span></div>
  </article>
</section>

<section class="section newsletter">
  <h4><svg width="10" height="8" viewBox="0 0 10 8" aria-hidden="true"><rect x=".5" y=".5" width="9" height="7" fill="none" stroke="#fff"/><path d="M.5 .5 5 4.5 9.5 .5" fill="none" stroke="#fff"/></svg>SIGN UP FOR NEWSLETTER</h4>
  <div class="email">Enter Your E-Mail Address</div>
  <div class="subscribe">SUBSCRIBE NOW</div>
</section>

<footer class="section site-footer">
  <div class="footer-col" style="left:80px">
    <h5>QUICK LINKS</h5>
    <ul><li>Home</li><li>Events</li><li>Blog</li><li>About</li><li>Dog Wash</li><li>Products</li><li>Resources</li><li>Contact</li></ul>
  </div>
  <div class="footer-col" style="left:165px">
    <h5>OTHER LINKS</h5>
    <ul><li>Policies</li><li>Return Policy</li><li>Privacy Policy</li><li>Employment</li><li>Staff Login</li></ul>
  </div>
  <div class="footer-col" style="left:254px"><h5><i></i>PAGEWALL FEEDS</h5></div>
  <div class="page-box">
    <div class="head">Find us on Pagewall</div>
    <div class="brand-row"><b>LARCH CRITTER DEPOT</b><span class="like">Like</span><span class="count">200</span></div>
    <div class="avatars">
      <div class="avatar"><div class="pic" role="img" aria-label="Follower photo"></div>Mira</div>
      <div class="avatar"><div class="pic" role="img" aria-label="Follower photo"></div>Tobin</div>
      <div class="avatar"><div class="pic" role="img" aria-label="Follower photo"></div>Levent</div>
      <div class="avatar"><div class="pic" role="img" aria-label="Follower photo"></div>Kaden</div>
      <div class="avatar"><div class="pic" role="img" aria-label="Follower photo"></div>Wes</div>
    </div>
    <div class="foot"><i></i>Pagewall social plugin</div>
  </div>

  <div class="footer-col" style="left:414px"><h5><i></i>CHIRPLINE FEEDS</h5></div>
  <div class="slide-arrows">‹ ›</div>

  <div class="tweet" style="top:60px">
    <div class="thumb" role="img" aria-label="Cat and dog illustration" style="background:linear-gradient(#efe6d2,#c9a46a)"></div>
    <div class="body">
      <div class="handle">Larch Critter Depot@LarchCritter Nov 20</div>
      <div class="text">This bag of food is just $6 at LCD and will be donated to a cat in need! SHARE food bank needs your donations!</div>
    </div>
    <div class="actions">
      <svg width="6" height="6" viewBox="0 0 6 6" aria-hidden="true"><path d="M5 5V3H1.5M3 1 1 3l2 2" fill="none" stroke="#fff" stroke-width="1"/></svg>
      <svg width="7" height="6" viewBox="0 0 7 6" aria-hidden="true"><path d="M1 4V1h4M6 2v3H2" fill="none" stroke="#fff" stroke-width="1"/></svg>
      <svg width="6" height="6" viewBox="0 0 6 6" aria-hidden="true"><path d="M3 5.5 .6 3A1.3 1.3 0 0 1 3 1.3 1.3 1.3 0 0 1 5.4 3z" fill="#fff"/></svg>
    </div>
  </div>

  <div class="tweet" style="top:129px">
    <div class="thumb" role="img" aria-label="Partner clinic emblem" style="background:#fff"></div>
    <div class="body">
      <div class="handle">Larch Critter Depot@LarchCritter Nov 20</div>
      <div class="text">This bag of food is just $6 at LCD and will be donated to a cat in need! SHARE food bank needs your donations!</div>
    </div>
    <div class="actions">
      <svg width="6" height="6" viewBox="0 0 6 6" aria-hidden="true"><path d="M5 5V3H1.5M3 1 1 3l2 2" fill="none" stroke="#fff" stroke-width="1"/></svg>
      <svg width="7" height="6" viewBox="0 0 7 6" aria-hidden="true"><path d="M1 4V1h4M6 2v3H2" fill="none" stroke="#fff" stroke-width="1"/></svg>
      <svg width="6" height="6" viewBox="0 0 6 6" aria-hidden="true"><path d="M3 5.5 .6 3A1.3 1.3 0 0 1 3 1.3 1.3 1.3 0 0 1 5.4 3z" fill="#fff"/></svg>
    </div>
  </div>

  <div class="footer-bottom">
    <span class="copy">© 2015 COMPANY NAME | ALL RIGHTS RESERVED</span>
    <span class="connect">CONNECT WITH US &nbsp;<span class="social-dots"><i></i><i></i><i></i><i></i><i></i><i></i></span></span>
  </div>
</footer>

</body>
</html>
```